KVR Inc Web Design

WHAT ARE WE DOING?
We are developing a new website look and feel for a new company called KVR Inc. This new look and feel should include colors, design elements, choice of photography and other imagery, fonts, and other user experience elements.

WHAT DO THEY DO?
KVR, Inc, makes tools for researchers who are studying protein-protein interactions. These molecules are the basic tools of biology, and serve as key targets for drug developers and disease researchers. The world of proteins is enormously complex, and companies like KVR provide researchers with critical tools that help them elucidate this world.

WHO ARE WE TALKING TO?
The target audience for this website are professional scientists working in university research or biopharma drug development. They are highly sophisticated consumers looking for key tools that will advance their research.

WHAT DO WE WANT THEM TO DO?
The site is an information resource for the customer exploring the tools that KVR sells and the scientific issues surrounding protein-protein interactions. They should be able to navigate easily to their content of choice, while the whole site should convey a professionalism that enhanced KVR’s credibility.

WHAT DOES THE KVR BRAND STAND FOR?
KVR stands for illumination. Proteins are challenging to study, and KVR exists to help shed light on their workings.

WHAT ARE THE KEY VALUES OF THE KVR BRAND?
Integrity. Innovation. Insight.

WHAT ARE THE EXECUTIONAL MANDITORIES?
The look and feel is completely up for grabs. Nothing is off the table.

WHAT ARE THE DELIVERABLES?
We need new designs for the following templates:
http://cms.marlowbench.com/
http://cms.marlowbench.com/products-and-services/instruments-3/bench-top-instruments/
http://cms.marlowbench.com/category/lab-study/

```html
<!DOCTYPE html>
<html lang="en">
<head>
<meta charset="utf-8">
<title>KVR Inc</title>
<link rel="stylesheet" href="https://fonts.googleapis.com/css2?family=Mulish:wght@400;600;700&family=Open+Sans:wght@400&display=swap">
<style>
:root{
  --orange:#fdb84c;
  --orange-text:#f6a623;
  --brown:#6b5136;
  --dark:#5d5859;
  --text:#3a3a3a;
  --muted:#6a6a6a;
  --blue:#35b6df;
  --white:#ffffff;
  --card-edge:#e4e4e4;
}
*{margin:0;padding:0;box-sizing:border-box}
html,body{width:1200px;height:905px;overflow:hidden;background:var(--white);font-family:"Mulish",sans-serif}
.page{position:relative;width:1200px;height:905px}
.header-band{position:absolute;left:0;top:0;width:1200px;height:452px;background:var(--orange)}
.brand{position:absolute;left:161px;top:16px;color:var(--white);font-size:26px;font-weight:400;letter-spacing:6px}
.nav{position:absolute;left:323px;top:17px;display:flex;list-style:none}
.nav li{height:28px;line-height:28px;padding:0 10px;color:var(--white);font-weight:700;font-size:14px}
.nav li.active{background:var(--brown);border-radius:14px;padding:0 12px}
.search{position:absolute;left:913px;top:20px;width:126px;height:23px;background:#c79a4a;color:#f3e3c4;font-size:12px;line-height:23px;padding-left:7px}
.search svg{position:absolute;right:5px;top:5px}
.hero{position:absolute;left:162px;top:61px;width:876px;height:405px;background:linear-gradient(100deg,#e9e9e9 0%,#cfcfcf 35%,#dedede 55%,#c8b7a6 75%,#e8e8e8 100%);box-shadow:0 6px 10px rgba(0,0,0,.08)}
.hero-copy{position:absolute;left:227px;top:226px;color:var(--text);font-size:14px;line-height:21px}
.btn{display:inline-block;background:var(--dark);color:var(--white);border-radius:15px;text-align:center}
.hero-btn{position:absolute;left:223px;top:281px;width:118px;height:28px;line-height:28px;font-size:12.5px}
.dots{position:absolute;left:964px;top:411px;display:flex;gap:4px}
.dots span{width:10px;height:10px;border-radius:50%;background:#222;border:2px solid var(--white)}
.dots span.on{background:var(--orange-text)}
.ticker{position:absolute;left:265px;top:435px;width:670px;height:30px;line-height:30px;background:var(--blue);color:var(--white);border-radius:15px;text-align:center;font-size:12.3px}
.card{position:absolute;top:481px;width:284px;height:277px;background:#f4f4f4;box-shadow:inset 0 0 18px var(--card-edge)}
.card-inner{position:absolute;left:26px;top:30px;right:26px;bottom:21px;background:var(--white);text-align:center}
.card-icon{position:absolute;left:50%;top:4px;margin-left:-34px}
.card h2{position:absolute;top:72px;left:0;right:0;color:var(--orange-text);font-size:19px;font-weight:700;letter-spacing:.5px}
.card p{position:absolute;top:101px;left:-12px;right:-12px;color:var(--text);font-size:12.3px;line-height:17px}
.card .btn{position:absolute;top:218px;left:50%;margin-left:-64px;width:127px;height:28px;line-height:28px;font-size:14px}
.footer-rule{position:absolute;left:588px;top:792px;width:25px;height:3px;background:linear-gradient(90deg,var(--orange-text) 40%,var(--dark) 40%,var(--dark) 60%,var(--orange-text) 60%)}
.footer-links{position:absolute;top:806px;left:0;width:1200px;text-align:center;color:var(--muted);font-size:12px}
.copyright{position:absolute;top:824px;left:0;width:1200px;text-align:center;color:var(--muted);font-family:"Open Sans",sans-serif;font-size:12px}
.social{position:absolute;top:847px;left:569px;display:flex;gap:4px}
.social span{width:18px;height:18px;border-radius:50%;background:var(--dark)}
</style>
</head>
<body>
<div class="page">
  <div class="header-band"></div>
  <div class="brand">KVR INC</div>
  <ul class="nav">
    <li>Company</li>
    <li class="active">Products &amp; Services</li>
    <li>Learning Center</li>
    <li>Events</li>
    <li>KVR News</li>
    <li>Contact</li>
  </ul>
  <div class="search">Search
    <svg width="13" height="13" viewBox="0 0 13 13"><circle cx="5.5" cy="5.5" r="4" fill="none" stroke="#f3e3c4" stroke-width="1.5"/><line x1="8.5" y1="8.5" x2="12" y2="12" stroke="#f3e3c4" stroke-width="1.8"/></svg>
  </div>

  <div class="hero" role="img" aria-label="Scientist in safety glasses examining a test tube beside a microscope in a bright lab"></div>
  <p class="hero-copy">Lorem ipsum dolor sit amet, consectetur<br>Proin placerat nulla amer massa, condimentum..</p>
  <span class="btn hero-btn">Call to Action</span>
  <div class="dots"><span class="on"></span><span></span><span></span><span></span></div>
  <div class="ticker">October 7, 2013 : Lorem ipsum dolor sit amet, consecteturelusmod&nbsp; adipisicing elit, sed do eiusmod tempor&nbsp; &gt;&gt;&gt;</div>

  <section class="card" style="left:160px">
    <div class="card-inner">
      <svg class="card-icon" width="68" height="78" viewBox="0 0 68 78">
        <polygon points="34,1 66,19.5 66,58.5 34,77 2,58.5 2,19.5" fill="#fff" stroke="#d8d8d8" stroke-width="1.5"/>
        <path d="M30 24h8v3h-1v10l9 15c1 2 0 4-2 4H24c-2 0-3-2-2-4l9-15V27h-1z" fill="#676364"/>
        <circle cx="36" cy="19" r="1.6" fill="#676364"/><circle cx="32" cy="16" r="1.2" fill="#676364"/>
      </svg>
      <h2>Innovation</h2>
      <p>Lorem ipsum dolor sit amet, consectetur adipiscing elit. Proin placerat nulla amer massa, condimentum leo...</p>
      <span class="btn">Learn More</span>
    </div>
  </section>

  <section class="card" style="left:458px">
    <div class="card-inner">
      <svg class="card-icon" width="68" height="78" viewBox="0 0 68 78">
        <polygon points="34,1 66,19.5 66,58.5 34,77 2,58.5 2,19.5" fill="#fff" stroke="#d8d8d8" stroke-width="1.5"/>
        <rect x="29" y="20" width="8" height="16" rx="2" transform="rotate(-35 33 28)" fill="#676364"/>
        <path d="M26 36a12 12 0 0 0 14 16" fill="none" stroke="#676364" stroke-width="4"/>
        <rect x="33" y="39" width="10" height="4" fill="#676364"/>
        <rect x="24" y="52" width="24" height="5" rx="1" fill="#676364"/>
      </svg>
      <h2>Automation</h2>
      <p>Lorem ipsum dolor sit amet, consectetur adipiscing elit. Proin placerat nulla amer massa, condimentum leo...</p>
      <span class="btn">Order Today</span>
    </div>
  </section>

  <section class="card" style="left:756px">
    <div class="card-inner">
      <svg class="card-icon" width="68" height="78" viewBox="0 0 68 78">
        <polygon points="34,1 66,19.5 66,58.5 34,77 2,58.5 2,19.5" fill="#fff" stroke="#d8d8d8" stroke-width="1.5"/>
        <circle cx="36" cy="34" r="9" fill="none" stroke="#676364" stroke-width="4"/>
        <line x1="29" y1="41" x2="19" y2="51" stroke="#676364" stroke-width="5" stroke-linecap="round"/>
        <circle cx="46" cy="44" r="2.5" fill="#676364"/><circle cx="50" cy="36" r="1.8" fill="#676364"/><circle cx="42" cy="50" r="1.8" fill="#676364"/>
      </svg>
      <h2>Research</h2>
      <p>Lorem ipsum dolor sit amet, consectetur adipiscing elit. Proin placerat nulla amer massa, condimentum leo...</p>
      <span class="btn">The Challenge</span>
    </div>
  </section>

  <div class="footer-rule"></div>
  <p class="footer-links">Company &nbsp;-&nbsp; Products &amp; Services &nbsp;-&nbsp; Learning Center &nbsp;-&nbsp; Events &nbsp;-&nbsp; KVR News &nbsp;-&nbsp; Contact</p>
  <p class="copyright">Copyright © KVR Inc. 2013</p>
  <div class="social" aria-label="Social links"><span></span><span></span><span></span></div>
</div>
</body>
</html>
```